Landing Page / Waitlist

I would like a landing page for people to sign up for a waiting list. The text on the page should include (but is not limited to):
1) Main point: The accounting system you'll love
2) Secondary points:
a. Ruthlessly efficient
b. Quietly intelligent
c. Driven by AI
I've attached a file of our logo

The design should be simple, clean, and innovative - this is an ai company

```html
<!DOCTYPE html>
<html lang="en">
<head>
<meta charset="UTF-8">
<title>Ledger Nova – Waitlist</title>
<link rel="stylesheet" href="https://fonts.googleapis.com/css2?family=Montserrat:wght@300;400;500;600;700;800&display=swap">
<style>
  :root {
    --page-bg: #ebebeb;
    --white: #ffffff;
    --accent: #0aa6f5;
    --chevron: #1ea2f7;
    --hero-one: #1f3258;
    --hero-one-deep: #16223f;
    --footer-one: #34507f;
    --hero-two: #102350;
    --hero-two-deep: #050d22;
    --footer-two: #173a70;
    --hero-three: #0c2f6e;
    --hero-three-deep: #0a2458;
    --footer-three: #0a4599;
    --field-line: rgba(255,255,255,0.75);
    --field-text: rgba(255,255,255,0.7);
  }
  * { margin: 0; padding: 0; box-sizing: border-box; }
  html, body { width: 711px; height: 1200px; overflow: hidden; }
  body {
    background: var(--page-bg);
    font-family: "Montserrat", sans-serif;
    color: var(--white);
    position: relative;
  }
  .variant {
    position: absolute;
    left: 24px;
    width: 663px;
    height: 364px;
    overflow: hidden;
  }
  .variant--orbit { top: 27px; background: radial-gradient(ellipse at 75% 45%, var(--hero-one) 0%, var(--hero-one-deep) 80%); }
  .variant--analyst { top: 418px; background: linear-gradient(160deg, var(--hero-two) 0%, var(--hero-two-deep) 85%); }
  .variant--network { top: 809px; background: var(--hero-three-deep); }

  .hero-art { position: absolute; }
  .variant--orbit .hero-art {
    left: 354px; top: 20px; width: 309px; height: 330px;
    background: radial-gradient(circle at 50% 45%, rgba(120,190,255,0.55) 0%, rgba(60,120,210,0.35) 35%, rgba(31,50,88,0) 70%);
  }
  .variant--analyst .hero-art {
    left: 370px; top: 0; width: 293px; height: 331px;
    background: radial-gradient(ellipse at 65% 55%, rgba(90,170,255,0.5) 0%, rgba(40,100,200,0.3) 40%, rgba(16,35,80,0) 75%);
  }
  .variant--network .hero-art {
    left: 0; top: 0; width: 663px; height: 331px;
    background: radial-gradient(ellipse at 50% 45%, var(--hero-three) 0%, var(--hero-three-deep) 90%);
  }

  .content { position: absolute; left: 42px; top: 0; width: 320px; height: 331px; }
  .brand {
    position: absolute; top: 20px; left: 0;
    display: flex; flex-direction: column; align-items: center; width: 122px;
  }
  .brand__mark { width: 32px; height: 32px; background: var(--accent); margin-bottom: 9px; }
  .brand__name { font-weight: 600; font-size: 17px; letter-spacing: -0.3px; white-space: nowrap; }

  .headline { position: absolute; top: 117px; left: 0; white-space: nowrap; line-height: 1.3; }
  .headline__main { display: block; font-weight: 800; font-size: 23.5px; }
  .headline__sub { display: block; font-weight: 300; font-size: 24px; }

  .benefits { position: absolute; top: 184px; left: 0; width: 200px; list-style: none; }
  .benefits li { display: flex; align-items: center; height: 18px; font-size: 9.2px; font-weight: 400; white-space: nowrap; }
  .benefits svg { flex: none; width: 8px; height: 8px; margin-right: 11px; }

  .signup { position: absolute; top: 253px; left: 0; width: 260px; height: 23px; display: flex; }
  .signup__field {
    flex: 1; border: 0.8px solid var(--field-line); border-right: none; border-radius: 4px 0 0 4px;
    font-size: 8px; color: var(--field-text); display: flex; align-items: center; padding-left: 11px; white-space: nowrap;
  }
  .signup__button {
    flex: none; width: 84px; background: var(--accent); border-radius: 4px; margin-left: -1px;
    font-size: 8px; font-weight: 600; display: flex; align-items: center; justify-content: center; white-space: nowrap;
  }

  .footer {
    position: absolute; left: 0; bottom: 0; width: 663px; height: 33px;
    display: flex; align-items: center; justify-content: space-between; padding: 0 42px;
  }
  .variant--orbit .footer { background: var(--footer-one); }
  .variant--analyst .footer { background: var(--footer-two); }
  .variant--network .footer { background: var(--footer-three); }
  .footer__copy { font-size: 7.2px; white-space: nowrap; }
  .social { display: flex; gap: 2.5px; }
  .social span { width: 14px; height: 14px; border: 0.8px solid var(--white); border-radius: 2px; }

  .variant--network .centered { position: absolute; left: 0; top: 0; width: 663px; height: 331px; text-align: center; }
  .variant--network .brand { position: static; margin: 40px auto 0; width: auto; }
  .variant--network .brand__mark { width: 40px; height: 40px; margin-bottom: 8px; }
  .variant--network .brand__name { font-size: 25px; }
  .variant--network .headline { position: static; margin-top: 14px; line-height: 1.2; }
  .variant--network .headline__main { font-size: 30px; }
  .variant--network .headline__sub { font-size: 30px; }
  .inline-benefits { margin-top: 12px; display: flex; justify-content: center; align-items: center; gap: 10px; font-size: 9.5px; white-space: nowrap; }
  .inline-benefits i { width: 5px; height: 5px; border-radius: 50%; background: var(--chevron); display: inline-block; }
  .variant--network .signup { position: absolute; top: 251px; left: 183px; width: 296px; height: 24px; }
  .variant--network .signup__field { font-size: 8.5px; padding-left: 13px; }
  .variant--network .signup__button { width: 84px; font-size: 8.5px; }
</style>
</head>
<body>

<svg width="0" height="0" style="position:absolute">
  <defs>
    <symbol id="chevrons" viewBox="0 0 10 10">
      <path d="M1 1.5 L4.5 5 L1 8.5 M5 1.5 L8.5 5 L5 8.5" fill="none" stroke="#1ea2f7" stroke-width="1.6"/>
    </symbol>
  </defs>
</svg>

<section class="variant variant--orbit">
  <div class="hero-art" role="img" aria-label="Glowing digital globe with an AI chip and orbiting circuit lines"></div>
  <div class="content">
    <div class="brand"><span class="brand__mark"></span><span class="brand__name">LedgerNova</span></div>
    <h1 class="headline"><span class="headline__main">The Accounting System</span><span class="headline__sub">You’ll Love</span></h1>
    <ul class="benefits">
      <li><svg viewBox="0 0 10 10"><use href="#chevrons"/></svg>Ruthlessly efficient</li>
      <li><svg viewBox="0 0 10 10"><use href="#chevrons"/></svg>Quietly intelligent</li>
      <li><svg viewBox="0 0 10 10"><use href="#chevrons"/></svg>Driven by AI</li>
    </ul>
    <div class="signup"><div class="signup__field">Email Address</div><div class="signup__button">Join The Waitlist</div></div>
  </div>
  <footer class="footer">
    <span class="footer__copy">Copyright © 2025 Ledger Nova. All rights reserved.</span>
    <div class="social"><span></span><span></span><span></span><span></span></div>
  </footer>
</section>

<section class="variant variant--analyst">
  <div class="hero-art" role="img" aria-label="Glowing wireframe figure holding a tablet beside rising chart bars"></div>
  <div class="content">
    <div class="brand"><span class="brand__mark"></span><span class="brand__name">LedgerNova</span></div>
    <h1 class="headline"><span class="headline__main">The Accounting System</span><span class="headline__sub">You’ll Love</span></h1>
    <ul class="benefits">
      <li><svg viewBox="0 0 10 10"><use href="#chevrons"/></svg>Ruthlessly efficient</li>
      <li><svg viewBox="0 0 10 10"><use href="#chevrons"/></svg>Quietly intelligent</li>
      <li><svg viewBox="0 0 10 10"><use href="#chevrons"/></svg>Driven by AI</li>
    </ul>
    <div class="signup"><div class="signup__field">Email Address</div><div class="signup__button">Join The Waitlist</div></div>
  </div>
  <footer class="footer">
    <span class="footer__copy">Copyright © 2025 Ledger Nova. All rights reserved.</span>
    <div class="social"><span></span><span></span><span></span><span></span></div>
  </footer>
</section>

<section class="variant variant--network">
  <div class="hero-art" role="img" aria-label="Blue background of connected network nodes and lines"></div>
  <div class="centered">
    <div class="brand"><span class="brand__mark"></span><span class="brand__name">LedgerNova</span></div>
    <h1 class="headline"><span class="headline__main">The Accounting System</span><span class="headline__sub">You’ll Love</span></h1>
    <div class="inline-benefits"><span>Ruthlessly efficient</span><i></i><span>Quietly intelligent</span><i></i><span>Driven by AI</span></div>
    <div class="signup"><div class="signup__field">Email Address</div><div class="signup__button">Join The Waitlist</div></div>
  </div>
  <footer class="footer">
    <span class="footer__copy">Copyright © 2025 Ledger Nova. All rights reserved.</span>
    <div class="social"><span></span><span></span><span></span><span></span></div>
  </footer>
</section>

</body>
</html>
```